Card Design for my dog training business Brightpaw Obedience

Need a business card design for my dog training business with my new logo. Want the card to come off professional yet fun. Want it to be very eye catchy as well. I normally have these at vet clinics, pet stores, and groomers. so need it to look better than my competitors.
Target Market(s)
dog owners
Industry/Entity Type
Dog Training
Contact Information for Business Card
needs logo, my name and info
Font styles to use
Serif
Colors
0255a3
ffffff
ec1f27
000000
333333
fbfbfb
Requirements
Must have
- Brightpaw Obedience
- Felix Orland
- 415 903 2276
- info@brightpawobedience.example
- www.brightpawobedience.example

```html
<!DOCTYPE html>
<html lang="en">
<head>
<meta charset="utf-8">
<title>Brightpaw Obedience – Business Card</title>
<link rel="stylesheet" href="https://fonts.googleapis.com/css2?family=Cinzel:wght@500&family=Crimson+Text:ital@1&family=Roboto:wght@300&display=swap">
<style>
  :root {
    --backdrop: #e4e4e4;
    --card-white: #ffffff;
    --ink: #000000;
    --ink-soft: #333333;
    --card-black-top: #1a1b1c;
    --card-black-bottom: #070707;
    --mark-grey: #5c5c5c;
  }
  * { margin: 0; padding: 0; box-sizing: border-box; }
  html, body {
    width: 1125px;
    height: 1200px;
    overflow: hidden;
    background: var(--backdrop);
  }
  .canvas {
    position: relative;
    width: 1125px;
    height: 1200px;
  }
  .card {
    position: absolute;
    left: 151px;
    width: 824px;
    height: 471px;
  }
  .card--front {
    top: 98px;
    background: var(--card-white);
  }
  .card--back {
    top: 631px;
    background: linear-gradient(160deg, var(--card-black-top) 0%, var(--card-black-bottom) 100%);
  }
  .holder-name {
    position: absolute;
    left: 47px;
    top: 255px;
    font-family: "Cinzel", serif;
    font-weight: 500;
    font-size: 27px;
    letter-spacing: 1px;
    color: var(--ink);
  }
  .contact-list {
    position: absolute;
    left: 47px;
    top: 306px;
    list-style: none;
  }
  .contact-item {
    display: flex;
    align-items: center;
    height: 26.5px;
    font-family: "Roboto", sans-serif;
    font-weight: 300;
    font-size: 19px;
    color: var(--ink-soft);
  }
  .contact-icon {
    width: 18px;
    height: 18px;
    margin-right: 15px;
    fill: var(--ink-soft);
  }
  .tagline {
    position: absolute;
    left: 47px;
    top: 400px;
    font-family: "Crimson Text", serif;
    font-style: italic;
    font-size: 19.5px;
    color: var(--ink);
  }
  .brand-mark {
    position: absolute;
    left: 415px;
    top: 47px;
    width: 378px;
    height: 382px;
    display: flex;
    flex-direction: column;
    align-items: center;
    justify-content: center;
    font-family: "Cinzel", serif;
    font-weight: 500;
    color: var(--ink);
    text-align: center;
    line-height: 1.1;
  }
  .brand-mark__primary { font-size: 44px; letter-spacing: 1px; }
  .brand-mark__secondary { font-size: 30px; letter-spacing: 6px; }
  .brand-mark--small {
    left: 650px;
    top: 330px;
    width: 130px;
    height: 95px;
    color: var(--mark-grey);
  }
  .brand-mark--small .brand-mark__primary { font-size: 15px; }
  .brand-mark--small .brand-mark__secondary { font-size: 10px; letter-spacing: 2.5px; }
</style>
</head>
<body>
<main class="canvas">
  <section class="card card--front" aria-label="Business card front">
    <h1 class="holder-name">Felix Orland</h1>
    <ul class="contact-list">
      <li class="contact-item">
        <svg class="contact-icon" viewBox="0 0 24 24" aria-hidden="true"><path d="M6.6 10.8a15.2 15.2 0 0 0 6.6 6.6l2.2-2.2c.3-.3.7-.4 1-.2 1.1.4 2.3.6 3.6.6.6 0 1 .4 1 1V20c0 .6-.4 1-1 1A17 17 0 0 1 3 4c0-.6.4-1 1-1h3.5c.6 0 1 .4 1 1 0 1.3.2 2.5.6 3.6.1.3 0 .7-.2 1z"/></svg>
        415 903 2276
      </li>
      <li class="contact-item">
        <svg class="contact-icon" viewBox="0 0 24 24" aria-hidden="true"><path d="M2 6h20v12H2z M3.5 7.5 12 13l8.5-5.5" fill="none" stroke="#333333" stroke-width="2"/></svg>
        info@brightpawobedience.example
      </li>
      <li class="contact-item">
        <svg class="contact-icon" viewBox="0 0 24 24" aria-hidden="true"><circle cx="12" cy="12" r="9"/><path d="M8 7c2 0 3 1 2.5 3S8 11 9 14s-1 4-1 4M15 5c-1 2 1 3 3 3M14 14c2-1 4 0 4 2" fill="none" stroke="#ffffff" stroke-width="1.6"/></svg>
        brightpawobedience.example
      </li>
    </ul>
    <p class="tagline">“Training dogs across Texas one dog at a time.”</p>
    <div class="brand-mark">
      <span class="brand-mark__primary">BRIGHTPAW</span>
      <span class="brand-mark__secondary">OBEDIENCE</span>
    </div>
  </section>

  <section class="card card--back" aria-label="Business card back">
    <div class="brand-mark brand-mark--small">
      <span class="brand-mark__primary">BRIGHTPAW</span>
      <span class="brand-mark__secondary">OBEDIENCE</span>
    </div>
  </section>
</main>
</body>
</html>
```